IMPORTANT- PLEASE READ: Seeking Graphic (NOT a logo!)

**Please note**----This NOT a logo or branding project - we are looking for a specific graphic that conveys our core competency areas. See attached as an example (a very poor quality one but gives you an idea as to what we're looking for!)

**********************************************************************************************
The graphic should help convey the core competency areas (see below) that can extend off branches on a tree (just our idea, we are open to your suggestions).

Our international development program (called FarmPath) is developing a conceptual model that shows how we support development in agriculture and nutrition through providing what is called “extension services”. Extension is the input into a system (typically education/training or programming) that affects behavior change in people, therefore improving the way they do agriculture or approach nutrition. We also work on a series of cross-cutting areas that influence behavior change and agricultural and nutrition outcomes. More info on our website at www.farmpath.norvale.edu .

We are seeking assistance in developing a design/graphic that is dynamic, symbolic, and powerful, but also shows the relationships between extension and our major impact areas (primary):

-Agriculture
- Nutrition

and our cross-cutting themes (secondary):

-Climate Change and Environment
-Gender
-Youth
-Policy and Governance
-Capacity Building
-Research and Learning
-Technology

We came up with the idea of a tree, whereby the roots would be extension providing uptake of nutrients for the development of branches, which would be our impact areas and cross-cutting themes. This is only one idea we had and haven’t been able to get a decent graphic design for it. We are also very open to other representations of these relationships. Please note that our website’s color scheme is red/orange, yet agriculture has a green/blue color scheme, when making design choices.Visit our website to get a feel for our brand and work. www.farmpath.norvale.edu

Please be creative (you don't have to use the tree example!) and we look forwards to seeing what you design!

Target Market(s)

marketing materials for donors, partners and others

Industry/Entity Type

Education

Requirements
Must have
• Must LIST ALL CORE COMPETENCY AREAS (primary and secondary!) See above .
• Same colors as out existing branding platform- See www.farmpath.norvale.edu
Nice to have
Should not have
• Should NOT be a logo- we are NOT looking for a logo or branding materials. We need a GRAPHIC!!!!

```html
<!DOCTYPE html>
<html lang="en">
<head>
<meta charset="utf-8">
<title>FarmPath – Extension Competency Tree</title>
<link rel="stylesheet" href="https://fonts.googleapis.com/css2?family=Catamaran:wght@700;800&display=swap">
<style>
  :root {
    --bg: #f0f0f0;
    --ink: #2b1609;
    --red: #c0392b;
    --red-dark: #8e2a20;
    --orange: #e0702f;
    --orange-dark: #a84e1e;
    --olive: #7f8a3a;
    --olive-dark: #5b6429;
    --gold: #eb9a27;
    --gold-dark: #b8741a;
    --plum: #6b2146;
    --plum-dark: #4a1630;
    --label-text: #ffffff;
    --brand: #d9562a;
  }
  html, body {
    margin: 0;
    padding: 0;
    overflow: hidden;
    background: var(--bg);
  }
  .canvas {
    position: relative;
    width: 1200px;
    height: 1200px;
    overflow: hidden;
    background: var(--bg);
    font-family: "Catamaran", "Trebuchet MS", sans-serif;
  }
  .tree {
    display: block;
    width: 1200px;
    height: 1200px;
  }
  .branch { stroke: var(--ink); stroke-width: 6; fill: none; stroke-linejoin: miter; }
  .bud { fill: var(--ink); }
  .node { stroke: var(--ink); stroke-width: 6; }
  .tag rect { fill: var(--ink); }
  .tag text {
    fill: var(--label-text);
    font-family: "Catamaran", "Trebuchet MS", sans-serif;
    font-weight: 700;
    font-size: 21px;
    text-anchor: middle;
    dominant-baseline: central;
    letter-spacing: 0.3px;
  }
  .tag--primary text { font-size: 30px; font-weight: 800; }
  .tag--root text { font-size: 56px; font-weight: 800; letter-spacing: 1px; }
  .brand-name {
    position: absolute;
    right: 60px;
    bottom: 70px;
    margin: 0;
    color: var(--brand);
    font-family: "Catamaran", "Trebuchet MS", sans-serif;
    font-weight: 800;
    font-size: 46px;
    line-height: 1;
  }
</style>
</head>
<body>
<div class="canvas">
  <svg class="tree" viewBox="0 0 1500 1500" xmlns="http://www.w3.org/2000/svg" aria-labelledby="tree-title">
    <title id="tree-title">Extension feeding Nutrition and Agriculture and their cross-cutting themes</title>
    <defs>
      <linearGradient id="fill-red" x1="0" y1="0" x2="1" y2="1">
        <stop offset="0.5" stop-color="var(--red)"/><stop offset="0.5" stop-color="var(--red-dark)"/>
      </linearGradient>
      <linearGradient id="fill-orange" x1="0" y1="0" x2="1" y2="1">
        <stop offset="0.5" stop-color="var(--orange)"/><stop offset="0.5" stop-color="var(--orange-dark)"/>
      </linearGradient>
      <linearGradient id="fill-olive" x1="0" y1="0" x2="1" y2="1">
        <stop offset="0.5" stop-color="var(--olive)"/><stop offset="0.5" stop-color="var(--olive-dark)"/>
      </linearGradient>
      <linearGradient id="fill-gold" x1="0" y1="0" x2="1" y2="1">
        <stop offset="0.5" stop-color="var(--gold)"/><stop offset="0.5" stop-color="var(--gold-dark)"/>
      </linearGradient>
      <linearGradient id="fill-plum" x1="0" y1="0" x2="1" y2="1">
        <stop offset="0.5" stop-color="var(--plum)"/><stop offset="0.5" stop-color="var(--plum-dark)"/>
      </linearGradient>
    </defs>

    <!-- Nutrition branches -->
    <g class="branches branches--nutrition">
      <polyline class="branch" points="370,390 470,490"/>
      <polyline class="branch" points="322,460 445,468"/>
      <polyline class="branch" points="605,325 577,467"/>
      <polyline class="branch" points="490,310 585,405"/>
      <polyline class="branch" points="275,583 435,583"/>
      <polyline class="branch" points="296,678 385,588"/>
      <polyline class="branch" points="400,770 483,672"/>
      <polyline class="branch" points="378,702 455,702"/>
      <circle class="bud" cx="322" cy="460" r="12"/>
      <circle class="bud" cx="490" cy="310" r="12"/>
      <circle class="bud" cx="296" cy="678" r="12"/>
      <circle class="bud" cx="378" cy="702" r="12"/>
    </g>

    <!-- Agriculture branches -->
    <g class="branches branches--agriculture">
      <polyline class="branch" points="912,325 937,465"/>
      <polyline class="branch" points="850,403 925,402"/>
      <polyline class="branch" points="1215,407 1058,510"/>
      <polyline class="branch" points="1095,342 1117,467"/>
      <polyline class="branch" points="1078,582 1225,582"/>
      <polyline class="branch" points="1210,536 1135,580"/>
      <polyline class="branch" points="1040,665 1122,760"/>
      <polyline class="branch" points="1197,706 1080,705"/>
      <circle class="bud" cx="850" cy="403" r="12"/>
      <circle class="bud" cx="1095" cy="342" r="12"/>
      <circle class="bud" cx="1210" cy="536" r="12"/>
      <circle class="bud" cx="1197" cy="706" r="12"/>
    </g>

    <!-- Trunk lines -->
    <g class="trunk">
      <polyline class="branch" points="663,572 740,635 740,1292"/>
      <polyline class="branch" points="638,648 678,683 678,975 620,1065 620,1224"/>
      <polyline class="branch" points="678,423 790,525 825,560 828,650"/>
      <polyline class="branch" points="727,570 785,527"/>
      <polyline class="branch" points="862,632 800,672 800,1224"/>
      <polyline class="branch" points="805,820 862,912 862,1224"/>
      <polyline class="branch" points="645,1272 645,1292"/>
      <polyline class="branch" points="832,1272 832,1292"/>
      <circle class="bud" cx="678" cy="423" r="12"/>
      <circle class="bud" cx="727" cy="570" r="12"/>
    </g>

    <!-- Theme nodes -->
    <g class="nodes">
      <circle class="node node--primary" cx="548" cy="577" r="112" fill="url(#fill-red)" role="img" aria-label="Plate with fork and spoon icon for nutrition"/>
      <circle class="node node--primary" cx="962" cy="577" r="112" fill="url(#fill-gold)" role="img" aria-label="Wheat stalk icon for agriculture"/>
      <circle class="node" cx="322" cy="337" r="68" fill="url(#fill-red)" role="img" aria-label="Government building icon for governance"/>
      <circle class="node" cx="615" cy="257" r="68" fill="url(#fill-olive)" role="img" aria-label="Gavel icon for policy"/>
      <circle class="node" cx="910" cy="257" r="68" fill="url(#fill-olive)" role="img" aria-label="Globe and cloud icon for climate change and environment"/>
      <circle class="node" cx="1240" cy="340" r="68" fill="url(#fill-red)" role="img" aria-label="Puzzle piece icon for capacity building"/>
      <circle class="node" cx="208" cy="592" r="68" fill="url(#fill-orange)" role="img" aria-label="Gender symbols icon for gender"/>
      <circle class="node" cx="349" cy="817" r="68" fill="url(#fill-plum)" role="img" aria-label="Group icon for youth"/>
      <circle class="node" cx="1295" cy="590" r="68" fill="url(#fill-orange)" role="img" aria-label="Gears icon for technology"/>
      <circle class="node" cx="1169" cy="812" r="68" fill="url(#fill-plum)" role="img" aria-label="Light bulb icon for research and learning"/>
    </g>

    <!-- Labels -->
    <g class="tag"><rect x="241" y="200" width="167" height="52" rx="8"/><text x="324" y="227">GOVERNANCE</text></g>
    <g class="tag"><rect x="535" y="105" width="167" height="52" rx="8"/><text x="618" y="132">POLICY</text></g>
    <g class="tag"><rect x="810" y="100" width="225" height="73" rx="8"/><text x="922" y="123">CLIMATE CHANGE</text><text x="922" y="154">&amp; ENVIRONMENT</text></g>
    <g class="tag"><rect x="1155" y="184" width="167" height="73" rx="8"/><text x="1238" y="205">CAPACITY</text><text x="1238" y="236">BUILDING</text></g>
    <g class="tag"><rect x="125" y="457" width="167" height="52" rx="8"/><text x="208" y="484">GENDER</text></g>
    <g class="tag"><rect x="131" y="705" width="167" height="52" rx="8"/><text x="214" y="732">YOUTH</text></g>
    <g class="tag"><rect x="1210" y="458" width="168" height="52" rx="8"/><text x="1294" y="485">TECHNOLOGY</text></g>
    <g class="tag"><rect x="1240" y="691" width="167" height="73" rx="8"/><text x="1324" y="713">RESEARCH &amp;</text><text x="1324" y="744">LEARNING</text></g>
    <g class="tag tag--primary"><rect x="459" y="711" width="206" height="63" rx="8"/><text x="562" y="744">NUTRITION</text></g>
    <g class="tag tag--primary"><rect x="817" y="710" width="231" height="64" rx="8"/><text x="932" y="743">AGRICULTURE</text></g>
    <g class="tag"><rect x="563" y="1222" width="166" height="52" rx="8"/><text x="646" y="1250">EXTENSION</text></g>
    <g class="tag"><rect x="750" y="1222" width="166" height="52" rx="8"/><text x="833" y="1250">EXTENSION</text></g>
    <g class="tag tag--root"><rect x="526" y="1290" width="431" height="108" rx="10"/><text x="746" y="1347">EXTENSION</text></g>
  </svg>

  <p class="brand-name">FarmPath</p>
</div>
</body>
</html>
```